KorvaNest - Home Income and Business Resources Platform

I am looking for a website template for a multi-purposed website. This website will feature:

1.) Website Directory with Ratings & comments on listings
2.) Company Blog
3.) Homepage with Content (see files for homepage mock)

I would like the Design to have a default width 1170px (wider then normal)

Of course I am looking for Pages for Listings to be designed.

Great looking BLOG Layout: http://journal.plimworks.example/html/blog.html

I would like 4 Versions of a Website Directory Listing "Box"
1.) Basic Listing Box
2.) Sponsored Listing Box
3.) Recommended Listing Box
4.) Stay Away From Listing Box

Information on the Listing Page (Like on a Category Page)
Site Name, Site URL, Website Image, # of Views, Rating and # of Comments

Information on the Listing Details Page:
Same as ABOVE + About website Description, Vornic Score, Category Information

Decent looking examples is here: https://samples.trevolin.example/directory/computers/ and http://www.zqrankhub.example/.

I will include some sketches and screenshots of things I like/looking for. As designers,you have creative freedom and are encouraged to show this. This is Phase one of this project and winning designer is guaranteed to have future work for this project.

Target Market(s)

Directory, business, websites

Industry/Entity Type

Business

Coding

Coded - Design and coding required

Number of Pages Required

5+ page

Font styles to use
Sans Serif

Colors

Designer to choose colors to be used in the design.

Requirements
Must have
• Professional yet clean look. The use of Icons & images
• Unique Look
Should not have
• Any exact copies of any examples I provided

```html
<!DOCTYPE html>
<html lang="en">
<head>
<meta charset="utf-8">
<title>KorvaNest – About Us</title>
<link rel="stylesheet" href="https://fonts.googleapis.com/css2?family=Poppins:wght@700&family=Roboto+Condensed:wght@400;700&family=Open+Sans:wght@400&display=swap">
<style>
  :root {
    --sky-light: #8cc6e0;
    --sky-mid: #4fa3cf;
    --sky-deep: #3b7fb8;
    --sky-teal: #4cbad6;
    --white: #ffffff;
    --ink: #2b2b2b;
    --body-ink: #222222;
    --banner-a: #6e7f9e;
    --banner-b: #4d6088;
    --orb-a: #2a4f8e;
    --orb-b: #0c1a3e;
  }
  * { box-sizing: border-box; margin: 0; padding: 0; }
  html, body { width: 1200px; height: 952px; overflow: hidden; }
  body {
    position: relative;
    font-family: "Open Sans", Arial, sans-serif;
    background:
      radial-gradient(ellipse at 10% 85%, var(--sky-teal) 0%, transparent 55%),
      radial-gradient(ellipse at 5% 5%, var(--sky-light) 0%, transparent 45%),
      linear-gradient(135deg, var(--sky-mid) 0%, var(--sky-deep) 60%, var(--sky-mid) 100%);
  }
  .site-header { position: absolute; left: 0; top: 0; width: 1200px; height: 100px; }
  .brand {
    position: absolute; left: 99px; top: 30px;
    font-family: "Poppins", sans-serif; font-weight: 700;
    font-size: 40px; line-height: 52px; color: var(--white);
  }
  .main-nav { position: absolute; top: 43px; left: 0; width: 1200px; height: 32px; }
  .main-nav a {
    position: absolute; top: 0; height: 32px; line-height: 31px;
    font-family: "Roboto Condensed", sans-serif; font-size: 16px;
    color: var(--white); text-decoration: none; text-transform: uppercase;
  }
  .main-nav .is-active { border: 1px solid var(--white); border-radius: 3px; padding: 0 11px; }
  .content-card {
    position: absolute; left: 81px; top: 113px; width: 1037px; height: 656px;
    background: var(--white); border-radius: 26px;
    box-shadow: 0 4px 14px rgba(0,0,0,0.25);
  }
  .page-banner {
    position: absolute; left: 18px; top: 17px; width: 1002px; height: 229px;
    background: linear-gradient(90deg, var(--banner-a) 0%, #8a9bb8 45%, var(--banner-b) 100%);
  }
  .page-banner h1 {
    position: absolute; left: 43px; top: 93px;
    font-family: "Roboto Condensed", sans-serif; font-weight: 700;
    font-size: 40px; line-height: 44px; color: var(--white);
    text-shadow: 2px 2px 4px rgba(0,0,0,0.5);
  }
  .about-orb {
    position: absolute; left: 39px; top: 295px; width: 274px; height: 274px;
    border-radius: 50%; border: 4px solid #000;
    background: radial-gradient(circle at 50% 40%, #8fb2e6 0%, var(--orb-a) 30%, var(--orb-b) 80%);
  }
  .about-text { position: absolute; left: 351px; top: 300px; width: 655px; }
  .about-text h2 {
    font-family: "Roboto Condensed", sans-serif; font-weight: 400;
    font-size: 31px; line-height: 38px; color: var(--ink); text-transform: uppercase;
    margin-bottom: 20px;
  }
  .about-text p {
    font-size: 11.2px; line-height: 20.6px; color: var(--body-ink); margin-bottom: 14px;
  }
  .site-footer { position: absolute; left: 0; top: 828px; width: 1200px; text-align: center; }
  .social-list { display: flex; justify-content: center; gap: 13px; list-style: none; }
  .social-list li { width: 24px; height: 24px; background: var(--white); border-radius: 4px; }
  .footer-nav { margin-top: 14px; font-size: 13.7px; line-height: 18px; color: var(--white); }
  .footer-nav a { color: var(--white); text-decoration: none; }
  .footer-nav .sep { margin: 0 9px; }
  .copyright { margin-top: 13px; font-size: 12.4px; color: var(--white); }
</style>
</head>
<body>
  <header class="site-header">
    <div class="brand">KorvaNest</div>
    <nav class="main-nav">
      <a href="#" style="left:667px">Home</a>
      <a href="#" class="is-active" style="left:721px">About Us</a>
      <a href="#" style="left:827px">Our Services</a>
      <a href="#" style="left:955px">Blog</a>
      <a href="#" style="left:1017px">Contact Us</a>
    </nav>
  </header>

  <main class="content-card">
    <section class="page-banner" role="img" aria-label="Photo of a team meeting in a bright office">
      <h1>ABOUT US</h1>
    </section>
    <div class="about-orb" role="img" aria-label="Illustration of a glowing light bulb floating above an open hand"></div>
    <article class="about-text">
      <h2>Welcome to KorvaNest</h2>
      <p>Sed ut perspiciatis unde omnis iste natus error sit voluptatem accusantium doloremque laudantium, totam rem aperiam, eaque ipsa quae ab illo inventore veritatis et quasi architecto beatae vitae dicta sunt explicabo. Nemo enim ipsam voluptatem quia voluptas sit aspernatur aut odit aut fugit, sed quia consequuntur magni dolores eos qui ratione</p>
      <p>Nemo enim ipsam voluptatem quia voluptas sit aspernatur aut odit aut fugit, sed quia consequuntur magni dolores eos qui ratione voluptatem sequi nesciunt. Neque porro quisquam est, qui dolorem ipsum quia dolor sit amet, consectetur, adipisci velit, sed quia non numquam eius modi tempora incidunt ut labore et dolore magnam aliquam quaerat voluptatem. Ut enim ad minima veniam,</p>
      <p>Nemo enim ipsam voluptatem quia voluptas sit aspernatur aut odit aut fugit, sed quia consequuntur magni dolores eos qui ratione voluptatem sequi nesciunt. Neque porro quisquam est, qui dolorem ipsum quia dolor sit amet, consectetur, adipisci velit, sed quia non numquam eius modi tempora incidunt ut labore et dolore magnam aliquam</p>
    </article>
  </main>

  <footer class="site-footer">
    <ul class="social-list" aria-label="Social links">
      <li></li><li></li><li></li><li></li><li></li>
    </ul>
    <nav class="footer-nav">
      <a href="#">Home</a><span class="sep">/</span><a href="#">Contact</a><span class="sep">/</span><a href="#">services</a><span class="sep">/</span><a href="#">About Us</a><span class="sep">/</span><a href="#">Discussion</a><span class="sep">/</span><a href="#">Videos Links</a>
    </nav>
    <p class="copyright">Copyright @ 2017 KorvaNest. All Rights Reserved.</p>
  </footer>
</body>
</html>
```